Velmaro Partners Logo and Business Card Design

We already have the rough logo shape (however please make the lines on the logo much thicker so a dark background is not required to see it) . see photos uploaded.
It needs to be refined with color and digitized and then have a front and back business card layout done.
The services are high vibration healing support through a therapy and feng shui service offering. We want people to Feel Happiness, Feel Prosperity and Feel Peace. (the back of the card would have these phrases on it) So a warm, calm and peaceful feeling card.
We would like the card to use the logo provided (with thicker lines and color added) but below the graphic please use the name "Velmaro Partners" NOT Velmaro.
We also would like to use the colors in the colorized matrix shown in photos (gold and purple) but on the lighter side. Thanks for your time!

Front of Card should include: Logo, with Company Name: Velmaro Partners as part of logo, Name: Tomas Brekke email: tomas@velmaro.example web: www.velmaro.example mobile: 555.018.2264 at bottom of front list Family Constellation | Feng Shui

Back of Card should have the logo and the following listed vertically:

PERSONAL | BUSINESS (Larger size then smaller bullet items below)
*Find Happiness
*Find Prosperity
*Find Peace

Target Market(s)

Target market is both business and personal

Contact Information for Business Card

Front of Card should include: Logo, with Company Name: Velmaro Partners as part of logo, Name: Tomas Brekke email: tomas@velmaro.example web: www.velmaro.example mobile: 555.018.2264 at bottom of front list Family Constellation | Feng Shui ++++ Back of Card should have the logo and the following listed vertically: PERSONAL | BUSINESS (Larger size then smaller bullet items below) *Find Happiness *Find Prosperity *Find Peace

Font styles to use
Sans Serif

Colors

Designer to choose colors to be used in the design.

Requirements
Nice to have
• Nice light contrast color for the back of card background
Should not have
• No dark colored background on Card.

```html
<!DOCTYPE html>
<html lang="en">
<head>
<meta charset="utf-8">
<title>Velmaro Partners — Business Card</title>
<link href="https://fonts.googleapis.com/css2?family=Montserrat:wght@400;500;600;700&display=swap" rel="stylesheet">
<style>
  :root {
    --backdrop: #4a423d;
    --card-front: #fbf7ee;
    --card-back: #f1ecf8;
    --gold: #c99a17;
    --gold-light: #e6bd35;
    --gold-band: #e2b526;
    --violet: #7b5bc4;
    --ink: #3a3440;
    --ink-soft: #5c5566;
  }
  * { box-sizing: border-box; margin: 0; padding: 0; }
  html, body { width: 1200px; height: 786px; overflow: hidden; }
  body {
    background: var(--backdrop);
    font-family: "Montserrat", sans-serif;
    position: relative;
  }
  .card {
    position: absolute;
    top: 241px;
    width: 530px;
    height: 304px;
    border-radius: 4px;
    box-shadow: 0 14px 30px rgba(0,0,0,.45);
    overflow: hidden;
  }
  .card--front { left: 45px; background: var(--card-front); }
  .card--back  { left: 625px; background: var(--card-back); }

  .brand {
    position: absolute;
    left: 0; right: 0;
    display: flex;
    flex-direction: column;
    align-items: center;
  }
  .brand__dot {
    width: 50px; height: 50px;
    border: 5px solid var(--violet);
    border-radius: 50%;
    margin-bottom: 12px;
  }
  .brand__name {
    color: var(--gold);
    font-weight: 600;
    letter-spacing: 3px;
    text-transform: uppercase;
    white-space: nowrap;
  }
  .card--front .brand { top: 36px; }
  .card--front .brand__name { font-size: 23px; }

  .holder {
    position: absolute;
    right: 300px;
    top: 166px;
    text-align: right;
  }
  .holder__name {
    color: var(--gold);
    font-weight: 700;
    font-size: 19px;
    letter-spacing: 1px;
    text-transform: uppercase;
  }
  .holder__role { color: var(--ink-soft); font-size: 12px; margin-top: 2px; }

  .divider {
    position: absolute;
    left: 250px; top: 158px;
    width: 1.5px; height: 50px;
    background: var(--gold);
  }
  .contact {
    position: absolute;
    left: 266px; top: 156px;
    list-style: none;
  }
  .contact li {
    display: flex; align-items: center; gap: 8px;
    color: var(--ink);
    font-size: 12.5px;
    line-height: 18px;
  }
  .contact svg { width: 11px; height: 11px; flex: none; }
  .icon-fill { fill: var(--gold); }
  .icon-line { fill: none; stroke: var(--gold); stroke-width: 1.4; }

  .band {
    position: absolute;
    left: 0; right: 0;
    top: 226px; height: 46px;
    background: linear-gradient(90deg, var(--gold), var(--gold-band) 60%, #f0c93a);
    display: flex; align-items: center; justify-content: center;
    color: var(--ink);
    font-size: 13px;
    font-weight: 500;
  }

  .card--back .brand { top: 50px; }
  .card--back .brand__name { font-size: 26px; }
  .pill {
    position: absolute;
    left: 50%; top: 180px;
    transform: translateX(-50%);
    background: var(--gold-band);
    color: var(--ink);
    font-weight: 700;
    font-size: 14px;
    padding: 5px 16px;
    border-radius: 14px;
    white-space: nowrap;
  }
  .values {
    position: absolute;
    left: 0; right: 0; top: 222px;
    text-align: center;
    color: var(--ink);
    font-size: 12.5px;
    white-space: nowrap;
  }
  .values .sep { color: var(--gold); margin: 0 6px; }
</style>
</head>
<body>

  <section class="card card--front">
    <div class="brand">
      <span class="brand__dot"></span>
      <span class="brand__name">Velmaro Partners</span>
    </div>

    <div class="holder">
      <div class="holder__name">Tomas Brekke</div>
      <div class="holder__role">Owner</div>
    </div>
    <span class="divider"></span>
    <ul class="contact">
      <li><svg viewBox="0 0 12 12"><path class="icon-fill" d="M2 1h2.5l1 3-1.5 1a7 7 0 0 0 3 3l1-1.5 3 1V10a1 1 0 0 1-1 1A9 9 0 0 1 1 2a1 1 0 0 1 1-1z"/></svg>555.018.2264</li>
      <li><svg viewBox="0 0 12 12"><path class="icon-line" d="M1 2h10v8H1z M1 2l5 4 5-4"/></svg>tomas@velmaro.example</li>
      <li><svg viewBox="0 0 12 12"><circle class="icon-line" cx="6" cy="6" r="5"/><path class="icon-line" d="M1 6h10M6 1c-3 3-3 7 0 10M6 1c3 3 3 7 0 10"/></svg>www.velmaro.example</li>
    </ul>

    <div class="band">Family Constellation | Feng Shui</div>
  </section>

  <section class="card card--back">
    <div class="brand">
      <span class="brand__dot"></span>
      <span class="brand__name">Velmaro Partners</span>
    </div>
    <div class="pill">PERSONAL | BUSINESS</div>
    <p class="values">Find Happiness<span class="sep">•</span>Find Prosperity<span class="sep">•</span>Find Peace</p>
  </section>

</body>
</html>
```